refurbishment of diamond cut alloy wheels

we need to design a flyer that will catch the eye of the customer to refurbish diamond cut alloy wheels. we refurbish the wheels by using the latest CNC machine to precision cut and resurface the wheel. we would like before and after pictures of maybe Valtoren, KRT, Pelo wheels to give it a prestige look. The final design should communicate an expensive look and providing a good image for the business. The colours that I would like to use is black and red which should make the flyer stand out. The logo must sit on a black background without the wordings of specialists in GX, Pelo etc and also without servicing, diagnostics etc as well. This flyer is just to communicate refurbishment of alloy wheels to high standard.

Target Market(s)

any members of the public and car dealerships

Industry/Entity Type

Automotive

Colors

Requirements
Must have
• Wow factor with great images of wheels
Nice to have
• Maybe on the front of the flyer it has a picture of a wheel and then on the back of the flyer it has before and after pictures to show how just how incredible it is to refurbish wheels
Should not have
• other makes of wheels apart from KRT, Pelo, and any other high end makes of vehicles wheels

```html
<!DOCTYPE html>
<html lang="en">
<head>
<meta charset="utf-8">
<title>Kestrel Motors – Diamond Cut Alloy Wheel Refurbishment Flyer</title>
<link rel="stylesheet" href="https://fonts.googleapis.com/css2?family=Nunito:wght@700;800;900&family=Raleway:wght@300;400;500&display=swap">
<style>
  :root {
    --stage: #8e8e8e;
    --ink: #0b0b0c;
    --ink-soft: #17181a;
    --red: #c8242b;
    --red-deep: #93141a;
    --silver-light: #f1f1f1;
    --silver-mid: #b9bbbe;
    --silver-dark: #6d6f72;
    --white: #ffffff;
    --text-soft: #d8d8d8;
    --rule: #5b5c5e;
  }
  * { box-sizing: border-box; margin: 0; padding: 0; }
  html, body { width: 1200px; height: 3600px; overflow: hidden; }
  body { background: var(--stage); position: relative; font-family: "Raleway", sans-serif; color: var(--white); }

  .flyer {
    position: absolute; left: 100px; width: 1000px; height: 1410px; overflow: hidden;
    background: linear-gradient(180deg, var(--ink-soft) 0%, var(--ink) 60%, #050505 100%);
    box-shadow: 0 10px 30px rgba(0,0,0,.35);
  }
  .flyer--front { top: 250px; }
  .flyer--back { top: 1940px; }

  .abs { position: absolute; }

  /* brand */
  .brand { position: absolute; display: flex; align-items: center; gap: 18px; }
  .brand__mark { background: var(--red); flex: none; }
  .brand__name { font-family: "Nunito", sans-serif; font-weight: 900; color: var(--white); text-transform: uppercase; line-height: 1; letter-spacing: 1px; }

  /* front */
  .top-stripe { left: 0; top: 0; width: 680px; height: 38px; background: linear-gradient(90deg, var(--red-deep), var(--red)); clip-path: polygon(0 0, 100% 0, 95% 100%, 0 100%); }
  .top-stripe-edge { left: 0; top: 38px; width: 650px; height: 4px; background: linear-gradient(90deg, var(--silver-dark), var(--silver-light), var(--silver-dark)); }
  .brand-zone { left: 0; top: 42px; width: 560px; height: 260px; background: linear-gradient(180deg, #1a1b1d, #0d0d0e); }
  .brand--front { left: 70px; top: 140px; }
  .brand--front .brand__mark { width: 84px; height: 84px; }
  .brand--front .brand__name { font-size: 52px; }

  .photo { background-color: #222; }
  .photo--car-wheel { left: 0; top: 300px; width: 520px; height: 740px;
    background: radial-gradient(circle at 45% 65%, #3a3b3e 0%, #151517 45%, #070707 75%), #111;
    clip-path: polygon(0 0, 100% 0, 69% 100%, 0 100%); }
  .photo--car-wheel-accent { left: 0; top: 300px; width: 90px; height: 460px; background: linear-gradient(180deg, #d9b321, #a17f0e); clip-path: polygon(0 0, 100% 0, 30% 100%, 0 100%); opacity: .9; }
  .photo--spoke-wheel { left: 400px; top: 0; width: 600px; height: 800px;
    background: radial-gradient(circle at 62% 48%, #4a4d52 0%, #26282b 35%, #0c0c0d 70%);
    clip-path: polygon(27% 0, 100% 0, 100% 100%, 0 100%); }
  .photo-seam { left: 0; top: 0; width: 1000px; height: 1050px; pointer-events: none; }

  .headline-band { left: 330px; top: 790px; width: 670px; height: 250px;
    background: linear-gradient(180deg, var(--silver-light), var(--silver-dark));
    clip-path: polygon(12% 0, 100% 0, 100% 100%, 0 100%); }
  .headline-band__fill { position: absolute; left: 6px; top: 6px; right: 0; bottom: 0;
    background: linear-gradient(180deg, #d22b31 0%, var(--red) 40%, var(--red-deep) 100%);
    clip-path: polygon(12% 0, 100% 0, 100% 100%, 0 100%); }
  .headline { left: 430px; top: 812px; font-family: "Nunito", sans-serif; font-weight: 900; font-size: 62px; line-height: 72px; text-transform: uppercase; color: var(--white); letter-spacing: .5px; }
  .silver-bar { left: 0; top: 1040px; width: 1000px; height: 12px; background: linear-gradient(90deg, var(--silver-dark), var(--silver-light) 45%, var(--silver-mid) 70%, var(--silver-dark)); }

  .lead { left: 40px; top: 1090px; width: 920px; text-align: center; font-size: 36px; font-weight: 400; line-height: 46px; color: var(--white); }

  .rule { left: 65px; width: 870px; height: 2px; background: var(--rule); }
  .rule--front { top: 1245px; }
  .rule--back { top: 1250px; }

  .contact-note { left: 65px; top: 1305px; width: 460px; font-size: 23px; line-height: 30px; color: var(--text-soft); }

  .phone-button { position: absolute; left: 545px; width: 390px; height: 92px; border-radius: 16px;
    background: linear-gradient(180deg, var(--silver-light), var(--silver-dark)); padding: 4px; transform: skewX(-8deg); }
  .phone-button__face { width: 100%; height: 100%; border-radius: 12px; background: linear-gradient(180deg, #d8333a, var(--red) 45%, var(--red-deep));
    display: flex; align-items: center; justify-content: center; gap: 16px; }
  .phone-button__content { transform: skewX(8deg); display: flex; align-items: center; gap: 16px; }
  .phone-button__icon { width: 34px; height: 34px; }
  .phone-button__number { font-family: "Nunito", sans-serif; font-weight: 800; font-size: 42px; color: var(--white); letter-spacing: 1px; }
  .flyer--front .phone-button { top: 1283px; }
  .flyer--back .phone-button { top: 1290px; left: 555px; width: 380px; }

  /* back */
  .title-band { left: 0; top: 40px; width: 720px; height: 115px; background: linear-gradient(90deg, var(--red-deep), var(--red) 60%, #b01d23);
    clip-path: polygon(0 0, 100% 0, 93% 100%, 0 100%); }
  .title-band__text { left: 40px; top: 52px; font-family: "Nunito", sans-serif; font-weight: 700; font-size: 34px; line-height: 44px; color: var(--white); }
  .brand--back { left: 720px; top: 62px; gap: 12px; }
  .brand--back .brand__mark { width: 56px; height: 56px; }
  .brand--back .brand__name { font-size: 30px; line-height: 32px; }

  .compare-frame { top: 255px; height: 440px; padding: 6px;
    background: linear-gradient(160deg, var(--silver-light), var(--silver-dark) 60%, var(--silver-mid));
    clip-path: polygon(13% 0, 100% 0, 87% 100%, 0 100%); }
  .compare-frame--before { left: 55px; width: 475px; }
  .compare-frame--after { left: 520px; width: 430px; }
  .compare-frame__photo { width: 100%; height: 100%; clip-path: polygon(13% 0, 100% 0, 87% 100%, 0 100%); }
  .compare-frame--before .compare-frame__photo { background: radial-gradient(circle at 50% 50%, #9c9fa3 0%, #5a5c60 30%, #2a2b2e 60%, #6d6a63 100%); }
  .compare-frame--after .compare-frame__photo { background: radial-gradient(circle at 50% 50%, #c9ccd0 0%, #7b7f85 30%, #2b2d31 62%, #111 100%); }

  .compare-label { top: 672px; height: 62px; border-radius: 10px; padding: 3px;
    background: linear-gradient(180deg, var(--silver-light), var(--silver-dark)); }
  .compare-label__face { width: 100%; height: 100%; border-radius: 8px; background: linear-gradient(180deg, #d8333a, var(--red-deep));
    display: flex; align-items: center; justify-content: center; font-family: "Nunito", sans-serif; font-weight: 700; font-size: 34px; color: var(--white); }
  .compare-label--before { left: 120px; width: 350px; }
  .compare-label--after { left: 600px; width: 300px; }

  .service-area { left: 60px; top: 800px; width: 880px; text-align: center; font-size: 28px; line-height: 37px; color: var(--white); }
  .fine-print { left: 75px; width: 850px; text-align: center; font-size: 18px; line-height: 24px; color: var(--text-soft); }
  .fine-print--one { top: 935px; }
  .fine-print--two { top: 1020px; }

  .cta-small { left: 65px; top: 1294px; width: 470px; white-space: nowrap; font-size: 19px; line-height: 24px; text-transform: uppercase; letter-spacing: .5px; color: var(--text-soft); }
  .cta-large { left: 65px; top: 1324px; width: 470px; white-space: nowrap; font-size: 42px; line-height: 50px; font-weight: 400; text-transform: uppercase; letter-spacing: .5px; color: var(--white); }
</style>
</head>
<body>

<section class="flyer flyer--front" aria-label="Flyer front">
  <div class="abs top-stripe"></div>
  <div class="abs top-stripe-edge"></div>
  <div class="abs brand-zone"></div>

  <div class="abs photo photo--spoke-wheel" role="img" aria-label="Photo of a black multi-spoke alloy wheel close up"></div>
  <div class="abs photo photo--car-wheel" role="img" aria-label="Photo of a gloss black alloy wheel fitted on a yellow sports car"></div>
  <div class="abs photo--car-wheel-accent" aria-hidden="true"></div>

  <svg class="abs photo-seam" viewBox="0 0 1000 1050" aria-hidden="true">
    <defs>
      <linearGradient id="seam-silver" x1="0" y1="0" x2="0" y2="1">
        <stop offset="0" stop-color="#f1f1f1"/>
        <stop offset="1" stop-color="#6d6f72"/>
      </linearGradient>
    </defs>
    <line x1="562" y1="0" x2="402" y2="800" stroke="url(#seam-silver)" stroke-width="5"/>
    <line x1="0" y1="300" x2="520" y2="300" stroke="#2a2b2d" stroke-width="2"/>
  </svg>

  <div class="brand brand--front">
    <span class="brand__mark" aria-hidden="true"></span>
    <span class="brand__name">Kestrel Motors</span>
  </div>

  <div class="abs headline-band"><div class="headline-band__fill"></div></div>
  <h1 class="abs headline">Refurbish<br>Diamond Cut<br>Alloy Wheels</h1>
  <div class="abs silver-bar"></div>

  <p class="abs lead">We refurbish the wheels by using the latest CNC machine to precision cut and resurface the wheel.</p>

  <div class="abs rule rule--front"></div>
  <p class="abs contact-note">If you need premier Alloy Refurbishment services in Slough, please contact us:</p>

  <div class="phone-button">
    <div class="phone-button__face">
      <div class="phone-button__content">
        <svg class="phone-button__icon" viewBox="0 0 24 24" aria-hidden="true"><path fill="#fff" d="M6.6 10.8a15.1 15.1 0 0 0 6.6 6.6l2.2-2.2a1 1 0 0 1 1-.25 11.4 11.4 0 0 0 3.6.57 1 1 0 0 1 1 1V20a1 1 0 0 1-1 1A17 17 0 0 1 3 4a1 1 0 0 1 1-1h3.5a1 1 0 0 1 1 1c0 1.25.2 2.45.57 3.570a1 1 0 0 1-.25 1z"/></svg>
        <span class="phone-button__number">01632 960 418</span>
      </div>
    </div>
  </div>
</section>

<section class="flyer flyer--back" aria-label="Flyer back">
  <div class="abs title-band"></div>
  <h2 class="abs title-band__text">Alloy Refurbishment Specialists in<br>and around Slough</h2>

  <div class="brand brand--back">
    <span class="brand__mark" aria-hidden="true"></span>
    <span class="brand__name">Kestrel<br>Motors</span>
  </div>

  <div class="abs compare-frame compare-frame--before">
    <div class="compare-frame__photo" role="img" aria-label="Before photo of a worn diamond cut alloy wheel"></div>
  </div>
  <div class="abs compare-frame compare-frame--after">
    <div class="compare-frame__photo" role="img" aria-label="After photo of the same alloy wheel freshly diamond cut"></div>
  </div>

  <div class="abs compare-label compare-label--before"><div class="compare-label__face">Before</div></div>
  <div class="abs compare-label compare-label--after"><div class="compare-label__face">After</div></div>

  <p class="abs service-area">We cater to all locations in and around Colnbrook, Windsor, Hayes, Hounslow, Staines, Ascot and Ashford. For all car body modifications and restorations get in touch with our team of experts today!</p>

  <p class="abs fine-print fine-print--one">If you are looking to refresh the look of your car but don't want the expense of new alloys, with a wide range of limited edition colours to choose from why not consider customising and refurbishing your existing alloys?</p>

  <p class="abs fine-print fine-print--two">If you've had your alloy wheels long enough for them to require alloy refurbishment you can choose from a wide range of colours for refurbishment or choose a brand new set from our comprehensive range. At Crestline Wheels &amp; Tyres, we stock an extensive range of the latest designs from all the leading suppliers and manufacturers so you are sure to find a stylish new design.</p>

  <div class="abs rule rule--back"></div>
  <p class="abs cta-small">If your alloys need refurbishment</p>
  <p class="abs cta-large">Contact us today</p>

  <div class="phone-button">
    <div class="phone-button__face">
      <div class="phone-button__content">
        <svg class="phone-button__icon" viewBox="0 0 24 24" aria-hidden="true"><path fill="#fff" d="M6.6 10.8a15.1 15.1 0 0 0 6.6 6.6l2.2-2.2a1 1 0 0 1 1-.25 11.4 11.4 0 0 0 3.6.57 1 1 0 0 1 1 1V20a1 1 0 0 1-1 1A17 17 0 0 1 3 4a1 1 0 0 1 1-1h3.5a1 1 0 0 1 1 1c0 1.25.2 2.45.57 3.57a1 1 0 0 1-.25 1z"/></svg>
        <span class="phone-button__number">01632 960 418</span>
      </div>
    </div>
  </div>
</section>

</body>
</html>
```